Corwin Beacon Lighting - Commercial & Residential Landscape Lighting

Landscape Lighting Services & Design: Create a website for our landscape lighting company. We would like the design to be tailored around this description:
Illuminate with Confidence. Designed with Precision. Installed with Care.
Locally and veteran-owned, we take pride in transforming outdoor spaces through innovative lighting solutions tailored to your vision. From landscape and holiday lighting to permanent installations, our effortless process and expert design deliver breathtaking results and lasting curb appeal. Backed by a lifetime warranty and quarterly service options, our commitment to quality and customer satisfaction is unwavering. Try before you buy and experience your home in a whole new light with our complimentary demo kit — see the stunning effects before you decide.
- Also, add in this information as well; Outdoor Lighting not only beautifies spaces but also significantly enhances safety by illuminating your home or business. Beautifully lit entrances deter potential intruders, making your home a safer place for your loved ones. we also offer quarterly service plans to ensure lighting equipment continues to operate & illuminate effectively throughout the year. Also mention we provide free estimates and we are offering a 10% discount to military, veterans, and first responders.

Target Market(s)

Luxury market

Industry/Entity Type

Landscape Lighting - Residential & Commercial Lighting Services

Coding

Coded - Design and coding required

Number of Pages Required

2 page

Colors
00AB8E
00BBA5
67D7C9
C6EFE9
E9F9F6
59FF00
82FF00
B8FF75
E3FFCB
F4FFEA
FFC000
F8CF3A
FAE287
FDF2CF
FEFAEE

Requirements
Must have
• a lead generation button where people can submit their information for us to reach out to them and schedule their free estimate, homepage, about page, contact page, products and services page, user friendly, easy to navigate, and it also must be engaging and eye popping, as well as appealing to the luxury market. Please use colors; verdent green, dark green, ivory, and sunny yellow. Also, include an about page that references our story; Derek is retired Army and he opened a fitness studio in 2017 with his wife Jolene. He has installed low voltage lighting in every home he lived in and for his friends and family over the years and decided to open his own business because he is passionate about beautifying outdoor landscapes and highlighting a properties full potential, not only in the day but at night as well all while providing safety and security for his clients. Having a deep respect for nature and landscaping, he wants to provide the same care and quality to each of his clients as he has in the fitness industry for decades. He believes small businesses are the back bone of America and he's excited to provide a service that is all to often neglected in the design of a home.
Nice to have
• I would like to have a clear intent and purpose, engaging web design, clear call to action, optimized for search engines, mobile friendy design, security measures, credibility indicators

```html
<!DOCTYPE html>
<html lang="en">
<head>
<meta charset="utf-8">
<title>Corwin Beacon Lighting – Residential &amp; Commercial Landscape Lighting</title>
<link rel="stylesheet" href="https://fonts.googleapis.com/css2?family=Jost:wght@400;500;600&family=Montserrat:wght@400;500;600;700&display=swap">
<style>
:root{
  --forest:#0c3320;
  --forest-deep:#0a2c1b;
  --sun:#fccf22;
  --ivory:#ffffff;
  --mist:#f1f1f1;
  --ink:#1b1b1b;
  --muted:#6b6b6b;
  --line:#dcdcdc;
}
*{box-sizing:border-box;margin:0;padding:0}
html,body{width:1200px;height:4057px;overflow:hidden}
body{position:relative;background:var(--ivory);font-family:"Montserrat",sans-serif;color:var(--ink)}
.abs{position:absolute}
.heading{font-family:"Jost",sans-serif;font-weight:500;text-transform:uppercase;letter-spacing:.5px}
.btn{position:absolute;display:flex;align-items:center;justify-content:center;gap:8px;border-radius:24px;font-weight:700;font-size:14px;text-transform:uppercase;letter-spacing:.3px;text-decoration:none;white-space:nowrap}
.btn-sun{background:var(--sun);color:var(--forest)}
.btn-forest{background:var(--forest);color:var(--sun)}
.btn .chev{width:14px;height:14px;border-radius:50%;background:currentColor;display:inline-flex;align-items:center;justify-content:center}
.btn .chev svg{width:8px;height:8px}
.social{display:flex;gap:6px}
.social span{width:30px;height:30px;border-radius:50%;border:1.5px solid #fff;display:block}

/* header */
.site-header{left:0;top:0;width:1200px;height:98px;background:var(--forest)}
.brand{display:flex;align-items:center;gap:8px;font-family:"Jost",sans-serif;color:var(--sun);font-weight:500}
.brand-dot{width:10px;height:10px;border-radius:50%;background:var(--sun)}
.brand-name{font-size:26px;letter-spacing:2px;line-height:1}
.brand-sub{font-size:9px;letter-spacing:1.6px;margin-top:3px}
.nav{font-size:14px;color:#fff}
.nav a{color:#fff;text-decoration:none;position:absolute;white-space:nowrap}
.nav a.active{color:var(--sun);text-decoration:underline;text-underline-offset:4px}

/* hero */
.hero{left:0;top:98px;width:1200px;height:574px;background:linear-gradient(180deg,#1c2a3a 0%,#25323c 35%,#3a3a2e 60%,#3f4a2a 78%,#4b5530 100%)}
.hero-title{left:143px;top:120px;font-size:40px;line-height:62px;color:#fff;font-weight:600}
.hero-copy{left:143px;top:252px;width:530px;font-size:18px;line-height:32px;color:#fff;font-weight:500}
.dots{left:580px;top:531px;display:flex;gap:5px}
.dots i{width:10px;height:10px;border-radius:50%;border:1.5px solid #fff;display:block}
.dots i.on{background:#fff}

/* section titles */
.section-title{position:absolute;left:0;width:1200px;display:flex;justify-content:center;align-items:center;gap:22px;font-size:36px}
.section-title::before,.section-title::after{content:"";width:96px;height:3px;background:currentColor}

/* services */
.services{left:0;top:672px;width:1200px;height:573px;background:var(--forest)}
.services .section-title{top:56px;color:#fff}
.services-sub{left:0;top:124px;width:1200px;text-align:center;color:#fff;font-size:18px;font-weight:500}
.service{position:absolute;top:180px;width:300px;text-align:center;color:#fff}
.service-icon{width:100px;height:100px;border-radius:50%;border:2px solid #fff;margin:40px auto 0}
.service h3{font-family:"Montserrat",sans-serif;font-weight:500;font-size:18px;margin-top:15px;white-space:nowrap}
.service p{font-size:13.5px;line-height:24px;margin-top:8px}
.arrow-btn{position:absolute;width:37px;height:37px;border-radius:50%;display:flex;align-items:center;justify-content:center}
.arrow-btn svg{width:12px;height:12px}

/* story */
.story-photo{left:143px;top:1309px;width:420px;height:420px;border-radius:50%;background:radial-gradient(circle at 55% 40%,#b88e6e 0%,#8d6a4e 22%,#4b5a3c 48%,#9aa0a3 75%,#c6c9cb 100%)}
.story-title{left:620px;top:1325px;font-size:36px;display:flex;align-items:center;gap:18px;color:var(--forest-deep)}
.story-title::after{content:"";width:96px;height:3px;background:var(--forest)}
.story-lead{left:619px;top:1383px;width:450px;font-size:15px;line-height:32px;font-weight:500}
.story-body{left:619px;top:1452px;width:438px;font-size:13.3px;line-height:24px;color:var(--muted);text-align:justify}

.photo{position:absolute;top:1788px;width:438px;height:278px;border-radius:14px}
.photo-res{left:143px;background:linear-gradient(160deg,#4b5975 0%,#7b7f92 35%,#2f3a2f 60%,#7a5e66 80%,#4c4a3f 100%)}
.photo-com{left:617px;background:linear-gradient(160deg,#2f4a2d 0%,#556e3a 30%,#5d6b7a 60%,#3b4650 100%)}
.caption{position:absolute;top:2092px;width:438px;text-align:center;font-size:18px;font-weight:500}
.safety{left:140px;top:2140px;width:920px;text-align:center;font-size:13.2px;line-height:24px;color:var(--muted)}

/* estimate band */
.estimate{left:0;top:2360px;width:1200px;height:335px;background:var(--sun)}
.estimate .section-title{top:83px;color:var(--forest-deep)}
.estimate-sub{left:0;top:149px;width:1200px;text-align:center;font-size:18px;font-weight:500;color:var(--forest-deep)}

/* testimonials */
.testimonials-title{top:2752px;color:var(--ink)}
.card{position:absolute;top:2870px;width:443px;height:183px;background:#fff;border-top:4px solid var(--forest);border-radius:10px;box-shadow:0 4px 14px rgba(0,0,0,.12)}
.card p{position:absolute;left:20px;right:20px;top:62px;text-align:center;font-size:13.5px;line-height:24px;color:var(--muted)}
.avatar{position:absolute;top:2830px;width:88px;height:88px;border-radius:50%;border:3px solid #fff}
.avatar-a{left:319px;background:linear-gradient(160deg,#58708c,#2c3d52)}
.avatar-b{left:789px;background:linear-gradient(160deg,#d9b98e,#a8855a)}
.reviewer{position:absolute;top:3070px;width:443px;text-align:center;font-size:18px;font-weight:500}
.stars{position:absolute;top:3096px;width:443px;display:flex;justify-content:center;gap:1px}
.stars svg{width:11px;height:11px}

/* contact */
.contact{left:0;top:3185px;width:1200px;height:505px;background:var(--mist)}
.contact .section-title{top:56px;color:var(--ink)}
.field{position:absolute;background:#fff;border:1px solid var(--line);font-size:13px;color:#888;display:flex;align-items:center;gap:6px;padding-left:17px}
.field svg{width:11px;height:11px}
.field.msg{align-items:flex-start;padding-top:14px}

/* footer */
.site-footer{left:0;top:3690px;width:1200px;height:367px;background:var(--forest)}
.footer-nav{left:0;top:195px;width:1200px;display:flex;justify-content:center;font-size:16px;color:#fff;gap:22px}
.footer-rule{left:143px;top:235px;width:912px;height:1px;background:rgba(255,255,255,.35)}
.copyright{left:0;top:262px;width:1200px;text-align:center;font-size:12.5px;color:#fff}
</style>
</head>
<body>

<header class="abs site-header">
  <div class="abs brand" style="left:143px;top:24px">
    <span class="brand-dot"></span>
    <div>
      <div class="brand-name">CORWIN</div>
      <div class="brand-sub">BEACON LIGHTING</div>
    </div>
  </div>
  <div class="abs social" style="left:722px;top:18px"><span></span><span></span><span></span><span></span></div>
  <a class="btn btn-sun" style="left:887px;top:13px;width:168px;height:38px;font-size:13px">Get Started <span class="chev"><svg viewBox="0 0 8 8"><path d="M3 1.5 5.5 4 3 6.5" stroke="#fccf22" stroke-width="1.6" fill="none"/></svg></span></a>
  <nav class="nav">
    <a class="active" style="left:455px;top:71px">HOME</a>
    <a style="left:565px;top:71px">ABOUT US</a>
    <a style="left:704px;top:71px">PRODUCTS</a>
    <a style="left:850px;top:71px">SERVICES</a>
    <a style="left:984px;top:71px">CONTACT</a>
  </nav>
</header>

<section class="abs hero" role="img" aria-label="Brick home with landscape lighting at dusk">
  <h1 class="abs heading hero-title">Designed with precision.<br>Installed with care.</h1>
  <p class="abs hero-copy">Locally and veteran-owned, we take pride in transforming outdoor spaces through innovative lighting solutions tailored to your vision.</p>
  <a class="btn btn-sun" style="left:143px;top:378px;width:315px;height:47px;font-size:15px">Schedule a free estimate <span class="chev"><svg viewBox="0 0 8 8"><path d="M3 1.5 5.5 4 3 6.5" stroke="#fccf22" stroke-width="1.6" fill="none"/></svg></span></a>
  <div class="abs dots"><i></i><i class="on"></i><i></i></div>
</section>

<section class="abs services">
  <h2 class="section-title heading">Services we offer</h2>
  <p class="abs services-sub">Sed ut perspiciatis unde omnis iste natus error sit voluptatem accusantium dolore</p>

  <div class="arrow-btn" style="left:39px;top:243px;background:#fff"><svg viewBox="0 0 12 12"><path d="M8 2 4 6l4 4" stroke="#0c3320" stroke-width="2" fill="none"/></svg></div>
  <div class="arrow-btn" style="left:1123px;top:243px;background:#fff"><svg viewBox="0 0 12 12"><path d="M4 2l4 4-4 4" stroke="#0c3320" stroke-width="2" fill="none"/></svg></div>

  <div class="service" style="left:122px">
    <div class="service-icon" role="img" aria-label="Pathway lighting icon"></div>
    <h3>Pathway &amp; Walkway Lighting</h3>
    <p>Lorem ipsum dolor sit amet, consectetur adipiscing elit, sed do</p>
  </div>
  <div class="service" style="left:449px">
    <div class="service-icon" role="img" aria-label="Permanent installation icon"></div>
    <h3>Permanent Installations</h3>
    <p>Lorem ipsum dolor sit amet, consectetur adipiscing elit, sed do</p>
  </div>
  <div class="service" style="left:777px">
    <div class="service-icon" role="img" aria-label="Maintenance technician icon"></div>
    <h3>Maintenance &amp; Repairs</h3>
    <p>Lorem ipsum dolor sit amet, consectetur adipiscing elit, sed do</p>
  </div>

  <a class="btn btn-sun" style="left:196px;top:440px;width:152px;height:43px">Read more <span class="chev"><svg viewBox="0 0 8 8"><path d="M3 1.5 5.5 4 3 6.5" stroke="#fccf22" stroke-width="1.6" fill="none"/></svg></span></a>
  <a class="btn btn-sun" style="left:523px;top:440px;width:152px;height:43px">Read more <span class="chev"><svg viewBox="0 0 8 8"><path d="M3 1.5 5.5 4 3 6.5" stroke="#fccf22" stroke-width="1.6" fill="none"/></svg></span></a>
  <a class="btn btn-sun" style="left:851px;top:440px;width:152px;height:43px">Read more <span class="chev"><svg viewBox="0 0 8 8"><path d="M3 1.5 5.5 4 3 6.5" stroke="#fccf22" stroke-width="1.6" fill="none"/></svg></span></a>
</section>

<div class="abs story-photo" role="img" aria-label="Portrait of the owner, arms crossed, outdoors"></div>
<h2 class="abs heading story-title">Our story</h2>
<p class="abs story-lead">Derek Is Retired Army And He Opened A Fitness Studio In 2017 With His Wife Jolene.</p>
<p class="abs story-body">He has installed low voltage lighting in every home he lived in for many years and he has installed low voltage lighting for his friends and family over the years and decided to open his own business because he is passionate about beautifying outdoor landscapes and highlighting a properties</p>
<a class="btn btn-sun" style="left:619px;top:1606px;width:160px;height:44px">Learn more <span class="chev"><svg viewBox="0 0 8 8"><path d="M3 1.5 5.5 4 3 6.5" stroke="#fccf22" stroke-width="1.6" fill="none"/></svg></span></a>

<div class="photo photo-res" role="img" aria-label="Modern home walkway lit by path lights at dusk"></div>
<div class="photo photo-com" role="img" aria-label="Stone steps with bollard lights among landscaped plants"></div>
<p class="caption" style="left:143px">Residential Landscape Lighting</p>
<p class="caption" style="left:617px">Commercial Landscape Lighting</p>
<p class="abs safety">Outdoor Lighting not only beautifies spaces but also significantly enhances safety by illuminating your home or business. Beautifully lit entrances deter potential intruders, making your home a safer place for your loved ones. we also offer quarterly service plans to ensure lighting equipment continues to operate &amp; illuminate effectively throughout the year.</p>
<a class="btn btn-sun" style="left:455px;top:2250px;width:288px;height:43px">Schedule a free estimate <span class="chev"><svg viewBox="0 0 8 8"><path d="M3 1.5 5.5 4 3 6.5" stroke="#fccf22" stroke-width="1.6" fill="none"/></svg></span></a>

<section class="abs estimate">
  <h2 class="section-title heading">Free estimate</h2>
  <p class="abs estimate-sub">We Are Offering A 10% Discount To Military, Veterans, and First Responders.</p>
  <a class="btn btn-forest" style="left:455px;top:210px;width:288px;height:43px">Schedule a free estimate <span class="chev"><svg viewBox="0 0 8 8"><path d="M3 1.5 5.5 4 3 6.5" stroke="#0c3320" stroke-width="1.6" fill="none"/></svg></span></a>
</section>

<h2 class="section-title heading testimonials-title">Client testimonials</h2>
<div class="arrow-btn" style="left:79px;top:2944px;background:#fff;border:1px solid #ccc"><svg viewBox="0 0 12 12"><path d="M8 2 4 6l4 4" stroke="#1b1b1b" stroke-width="2" fill="none"/></svg></div>
<div class="arrow-btn" style="left:1084px;top:2944px;background:var(--sun)"><svg viewBox="0 0 12 12"><path d="M4 2l4 4-4 4" stroke="#1b1b1b" stroke-width="2" fill="none"/></svg></div>

<div class="card" style="left:143px"><p>Sed ut perspiciatis unde omnis iste natus error sit voluptatem accusantium doloremque laudantium, totam rem aperiam, eaque ipsa quae ab illo inventore veritatis et quasi architecto beatae vitae dicta sunt explicabo.</p></div>
<div class="card" style="left:612px"><p>Sed ut perspiciatis unde omnis iste natus error sit voluptatem accusantium doloremque laudantium, totam rem aperiam, eaque ipsa quae ab illo inventore veritatis et quasi architecto beatae vitae dicta sunt explicabo.</p></div>
<div class="avatar avatar-a" role="img" aria-label="Client portrait"></div>
<div class="avatar avatar-b" role="img" aria-label="Client portrait"></div>
<p class="reviewer" style="left:143px">Marcus P</p>
<p class="reviewer" style="left:612px">Renee Holt V</p>
<div class="stars" style="left:143px">
  <svg viewBox="0 0 10 10"><polygon points="5,0 6.2,3.6 10,3.6 7,5.9 8.1,9.5 5,7.3 1.9,9.5 3,5.9 0,3.6 3.8,3.6" fill="#f5b400"/></svg><svg viewBox="0 0 10 10"><polygon points="5,0 6.2,3.6 10,3.6 7,5.9 8.1,9.5 5,7.3 1.9,9.5 3,5.9 0,3.6 3.8,3.6" fill="#f5b400"/></svg><svg viewBox="0 0 10 10"><polygon points="5,0 6.2,3.6 10,3.6 7,5.9 8.1,9.5 5,7.3 1.9,9.5 3,5.9 0,3.6 3.8,3.6" fill="#f5b400"/></svg><svg viewBox="0 0 10 10"><polygon points="5,0 6.2,3.6 10,3.6 7,5.9 8.1,9.5 5,7.3 1.9,9.5 3,5.9 0,3.6 3.8,3.6" fill="#f5b400"/></svg><svg viewBox="0 0 10 10"><polygon points="5,0 6.2,3.6 10,3.6 7,5.9 8.1,9.5 5,7.3 1.9,9.5 3,5.9 0,3.6 3.8,3.6" fill="#f5b400"/></svg>
</div>
<div class="stars" style="left:612px">
  <svg viewBox="0 0 10 10"><polygon points="5,0 6.2,3.6 10,3.6 7,5.9 8.1,9.5 5,7.3 1.9,9.5 3,5.9 0,3.6 3.8,3.6" fill="#f5b400"/></svg><svg viewBox="0 0 10 10"><polygon points="5,0 6.2,3.6 10,3.6 7,5.9 8.1,9.5 5,7.3 1.9,9.5 3,5.9 0,3.6 3.8,3.6" fill="#f5b400"/></svg><svg viewBox="0 0 10 10"><polygon points="5,0 6.2,3.6 10,3.6 7,5.9 8.1,9.5 5,7.3 1.9,9.5 3,5.9 0,3.6 3.8,3.6" fill="#f5b400"/></svg><svg viewBox="0 0 10 10"><polygon points="5,0 6.2,3.6 10,3.6 7,5.9 8.1,9.5 5,7.3 1.9,9.5 3,5.9 0,3.6 3.8,3.6" fill="#f5b400"/></svg><svg viewBox="0 0 10 10"><polygon points="5,0 6.2,3.6 10,3.6 7,5.9 8.1,9.5 5,7.3 1.9,9.5 3,5.9 0,3.6 3.8,3.6" fill="#f5b400"/></svg>
</div>

<section class="abs contact">
  <h2 class="section-title heading">Contact us</h2>
  <div class="field" style="left:180px;top:128px;width:409px;height:45px"><svg viewBox="0 0 12 12" fill="none" stroke="#888" stroke-width="1.2"><circle cx="6" cy="4" r="2.5"/><path d="M1.5 11.5c0-3 2-4.5 4.5-4.5s4.5 1.5 4.5 4.5"/></svg>First Name</div>
  <div class="field" style="left:611px;top:128px;width:409px;height:45px"><svg viewBox="0 0 12 12" fill="none" stroke="#888" stroke-width="1.2"><circle cx="6" cy="4" r="2.5"/><path d="M1.5 11.5c0-3 2-4.5 4.5-4.5s4.5 1.5 4.5 4.5"/></svg>Last Name</div>
  <div class="field" style="left:180px;top:197px;width:409px;height:45px"><svg viewBox="0 0 12 12"><rect x="0.5" y="2" width="11" height="8" fill="#888"/><path d="M0.5 2.5 6 7l5.5-4.5" stroke="#fff" fill="none"/></svg>Email Address</div>
  <div class="field" style="left:611px;top:197px;width:409px;height:45px"><svg viewBox="0 0 12 12"><path d="M6 11.5S2 7 2 4.5a4 4 0 0 1 8 0C10 7 6 11.5 6 11.5z" fill="#888"/><circle cx="6" cy="4.5" r="1.4" fill="#fff"/></svg>Location</div>
  <div class="field msg" style="left:180px;top:267px;width:839px;height:101px"><svg viewBox="0 0 12 12"><path d="M6 1.5c3 0 5.5 1.8 5.5 4s-2.5 4-5.5 4c-.6 0-1.2-.1-1.7-.2L1.5 10.5l.9-2.2C1.2 7.6.5 6.6.5 5.5c0-2.2 2.5-4 5.5-4z" fill="#888"/></svg>Message</div>
  <a class="btn btn-sun" style="left:517px;top:403px;width:166px;height:44px">Submit now <span class="chev"><svg viewBox="0 0 8 8"><path d="M3 1.5 5.5 4 3 6.5" stroke="#fccf22" stroke-width="1.6" fill="none"/></svg></span></a>
</section>

<footer class="abs site-footer">
  <div class="abs brand" style="left:514px;top:106px">
    <span class="brand-dot"></span>
    <div style="text-align:center">
      <div class="brand-name" style="font-size:40px;letter-spacing:3px">CORWIN</div>
      <div class="brand-sub" style="font-size:11px">BEACON LIGHTING</div>
    </div>
  </div>
  <div class="abs footer-nav">
    <span>HOME</span><span>|</span><span>ABOUT US</span><span>|</span><span>PRODUCTS</span><span>|</span><span>SERVICES</span><span>|</span><span>CONTACT</span>
  </div>
  <div class="abs footer-rule"></div>
  <p class="abs copyright">Copyright © 2025 Corwin Beacon Lighting - &nbsp;All Rights Reserved</p>
  <div class="abs social" style="left:529px;top:292px">
    <span></span><span style="background:var(--sun);border-color:var(--sun)"></span><span></span><span></span>
  </div>
</footer>

</body>
</html>
```